Vellisant - Quality health delivered at your door

Vellisant offers home and Community Based Services for adults who wish to continue live independently in their communities. We increase accessibility to health care, reduce health care delivery gap, reduce mortality and morbidity, reduce health while promoting healthy living in the comfort of our patients communities or homes.

We provide on site services and deliver high quality healthcare at your door. Our experienced physicians coordinate care with our certified nurse practitioners and provide chronic care management, physical therapy, rehabilitation and medications management.

Target Market(s)

Older population living in independent living facilities

Industry/Entity Type

Health Care

Contact Information for Business Card

Vellisant

Number of Pages Required

4 page

Font styles to use
Sans Serif

Colors

Designer to choose colors to be used in the design.

```html
<!DOCTYPE html>
<html lang="en">
<head>
<meta charset="utf-8">
<title>Vellisant – Quality health delivered at your door</title>
<link rel="stylesheet" href="https://fonts.googleapis.com/css2?family=Philosopher:wght@400;700&family=Open+Sans:wght@400;600;700&display=swap">
<style>
:root{
  --orange:#f7941d;
  --orange-soft:#f9a94a;
  --olive:#7c9a2a;
  --dark:#222222;
  --footer:#2b2b2b;
  --ink:#333333;
  --muted:#666666;
  --grey-bg:#f3f3f3;
  --white:#ffffff;
}
*{box-sizing:border-box;margin:0;padding:0}
html,body{width:1200px;height:2575px;overflow:hidden;background:var(--white)}
body{position:relative;font-family:"Open Sans",Arial,sans-serif;color:var(--ink)}
.abs{position:absolute}
.btn{position:absolute;display:flex;align-items:center;justify-content:center;background:var(--olive);color:var(--white);font-size:15px;border-radius:2px}
.heading{position:absolute;left:0;width:1200px;text-align:center;font-family:"Philosopher",sans-serif;font-size:37px;color:var(--ink)}
.rule{position:absolute;left:565px;width:70px;height:3px;background:var(--orange)}

/* top bar */
.topbar{left:0;top:0;width:1200px;height:46px;background:var(--dark)}
.topbar .btn{left:111px;top:0;width:177px;height:46px;font-size:13px;font-weight:600}
.social{position:absolute;display:flex;gap:22px}
.social span{width:18px;height:18px;border-radius:50%;background:#bdbdbd}

/* header */
.header{left:0;top:46px;width:1200px;height:114px;background:var(--white)}
.brand{position:absolute;left:118px;top:8px;width:140px;text-align:center}
.brand .dot{width:62px;height:62px;border-radius:50%;background:var(--orange);margin:0 auto 6px}
.brand .name{font-family:"Philosopher",sans-serif;font-size:21px;color:var(--ink);letter-spacing:1px}
.nav{position:absolute;top:47px;font-size:12px;font-weight:600;color:var(--ink)}

/* hero */
.hero{left:0;top:160px;width:1200px;height:515px;background:linear-gradient(100deg,#bcd4e6 0%,#e9eef0 40%,#d8dccf 70%,#9fb784 100%)}
.hero-title{left:0;top:325px;width:1236px;text-align:center;font-family:"Philosopher",sans-serif;font-weight:700;font-size:58px;color:#1f3a1a;letter-spacing:2px}
.hero-sub{left:0;top:395px;width:1236px;text-align:center;font-size:26px;font-weight:700;color:#1f3a1a}
.hero .btn{left:363px;top:311px;width:172px;height:44px}

/* services */
.service{position:absolute;top:592px;width:172px;height:173px;background:var(--orange);color:var(--white);text-align:center}
.service svg{margin-top:36px}
.service p{margin-top:18px;font-family:"Philosopher",sans-serif;font-size:14px;text-transform:uppercase}
.strip{left:0;top:675px;width:1200px;height:213px;background:var(--grey-bg)}
.tagline{left:150px;top:810px;width:900px;text-align:center;font-size:16px;font-weight:700;color:#555;line-height:27px}

/* help */
.help-photo{left:111px;top:1025px;width:422px;height:332px;background:linear-gradient(120deg,#e6eef2,#cfdde6 60%,#f2f4f5)}
.help-text{left:572px;top:1022px;width:522px;font-size:11.5px;line-height:21px;color:var(--muted)}

/* testimonials */
.testi-bg{left:0;top:1416px;width:1200px;height:469px;background:var(--grey-bg)}
.testi{position:absolute;top:1560px;width:300px;text-align:center}
.testi .quote{width:30px;height:30px;border-radius:50%;background:var(--orange);margin:0 auto 8px;display:flex;align-items:center;justify-content:center;color:#fff;font-family:Georgia,serif;font-size:22px;line-height:1;padding-top:8px}
.testi .avatar{width:88px;height:88px;border-radius:50%;border:3px solid var(--orange);background:linear-gradient(#d9b89c,#a77b5a);margin:0 auto}
.testi p{margin-top:26px;font-size:11.5px;line-height:20px;color:var(--ink)}
.testi .who{margin-top:12px;font-size:11px;color:var(--orange)}

/* cta */
.cta{left:0;top:1885px;width:1200px;height:167px;background:var(--orange)}
.cta h3{position:absolute;left:0;top:36px;width:1200px;text-align:center;color:var(--white);font-size:21px;font-weight:700}
.cta .btn{left:461px;top:85px;width:173px;height:46px;background:var(--orange-soft);font-size:13px}

/* work */
.work{position:absolute;top:2191px;width:309px}
.work .pic{height:173px;background:linear-gradient(120deg,#3d6fb0,#9fb8d4 55%,#e8ecef)}
.work h4{margin-top:20px;font-size:13px;font-weight:600;color:var(--ink)}
.work span{display:block;margin-top:4px;font-size:11px;color:#999}

/* footer */
.footer{left:0;top:2451px;width:1200px;height:124px;background:var(--footer)}
.footer .btn{left:111px;top:42px;width:172px;height:43px}
.footer .rights{position:absolute;left:0;top:84px;width:1200px;text-align:center;color:#ccc;font-size:11px}
.footer .brand .name{color:#d0d0d0;font-size:18px}
.footer .brand .dot{width:52px;height:52px;background:#8a8a8a}
</style>
</head>
<body>

<div class="abs topbar">
  <div class="btn">REQUEST A HOUSECALL</div>
  <div class="social" style="left:920px;top:14px"><span></span><span></span><span></span><span></span><span></span></div>
</div>

<div class="abs header">
  <div class="brand"><div class="dot"></div><div class="name">VELLISANT</div></div>
  <span class="nav" style="left:572px">HOME</span>
  <span class="nav" style="left:636px">ABOUT US</span>
  <span class="nav" style="left:721px">OUR SERVICES</span>
  <span class="nav" style="left:829px">NEWS &amp; EVENTS</span>
  <span class="nav" style="left:953px">CONTACT US</span>
  <span class="nav" style="left:1056px">BLOG</span>
</div>

<div class="abs hero" role="img" aria-label="Photo of a nurse caring for a smiling senior woman outdoors">
  <div class="btn">Request a Housecall</div>
</div>
<div class="abs hero-title">VELLISANT</div>
<div class="abs hero-sub">We Provide On Site Services And Deliver High Quality Healthcare At Your Door</div>

<div class="abs strip"></div>

<div class="service" style="left:111px">
  <svg width="52" height="52" viewBox="0 0 52 52" fill="none" stroke="#fff" stroke-width="3"><circle cx="26" cy="10" r="6" fill="#fff"/><path d="M8 34h36M14 34l6-14h12l6 14M10 44h32"/></svg>
  <p>Physical Therapy</p>
</div>
<div class="service" style="left:312px">
  <svg width="52" height="52" viewBox="0 0 52 52" fill="none" stroke="#fff" stroke-width="3"><path d="M26 16c-4-8-16-4-12 6l12 12 12-12c4-10-8-14-12-6z"/><path d="M6 40c8 0 12 6 20 6s12-6 20-6"/></svg>
  <p>Mental Health</p>
</div>
<div class="service" style="left:512px">
  <svg width="52" height="52" viewBox="0 0 52 52" fill="none" stroke="#fff" stroke-width="3"><path d="M14 8c6-2 8 2 12 2s6-4 12-2 6 12 2 20l-4 16-4-12h-12l-4 12-4-16c-4-8-4-18 2-20z"/></svg>
  <p>Dental Health</p>
</div>
<div class="service" style="left:713px">
  <svg width="52" height="52" viewBox="0 0 52 52" fill="#fff"><rect x="4" y="16" width="30" height="22"/><path d="M34 22h8l6 8v8H34z"/><circle cx="14" cy="42" r="5"/><circle cx="40" cy="42" r="5"/><path d="M17 21h4v5h5v4h-5v5h-4v-5h-5v-4h5z" fill="#f7941d"/></svg>
  <p>Transportation</p>
</div>
<div class="service" style="left:917px">
  <svg width="52" height="52" viewBox="0 0 52 52" fill="none" stroke="#fff" stroke-width="3"><circle cx="26" cy="26" r="22"/><path d="M26 15v22M15 26h22"/></svg>
  <p>View All</p>
</div>

<div class="abs tagline">Vellisant offers home and Community Based Services for adults who wish to continue to live independently in the comfort of their communities.</div>

<div class="heading" style="top:930px">How Can We Help You?</div>
<div class="rule" style="top:981px"></div>
<div class="abs help-photo" role="img" aria-label="Photo of a smiling doctor talking on the phone"></div>
<div class="abs help-text">The standard chunk of Lorem Ipsum used since the 1500s is reproduced below for those interested. Sections 1.10.32 and 1.10.33 from "de Finibus Bonorum et Malorum" by Cicero are also reproduced in their exact original form, accompanied by English versions from the 1914 translation by H. Rackham. The standard chunk of Lorem Ipsum used since the 1500s is reproduced below for those interested. Sections 1.10.32 and 1.10.33 from "de Finibus Bonorum et Malorum" by Cicero are also reproduced in their exact original form, accompanied by English versions from the 1914 translation by H. Rackham. The standard chunk of Lorem Ipsum used since the 1500s is reproduced below for those interested. Sections 1.10.32 and 1.10.33 from "de Finibus Bonorum et Malorum" by Cicero are also reproduced in their exact original form, accompanied by English versions from the 1914 translation by H. Rackham.</div>
<div class="btn" style="left:572px;top:1251px;width:175px;height:44px">Request a Housecall</div>

<div class="abs testi-bg"></div>
<div class="heading" style="top:1462px">How Can We Help You?</div>
<div class="rule" style="top:1512px"></div>
<div class="testi" style="left:115px"><div class="quote">&ldquo;</div><div class="avatar" role="img" aria-label="Customer portrait"></div><p>The standard chunk of Lorem Ipsum used since the 1500s is reproduced below for those interested. Sections 1.10.32 and 1.10.33 from "de Finibus Bonorum et Malorum" by Cicero are also reproduced in their exact original</p><div class="who">Wiral Customer Name</div></div>
<div class="testi" style="left:450px"><div class="quote">&ldquo;</div><div class="avatar" role="img" aria-label="Customer portrait"></div><p>The standard chunk of Lorem Ipsum used since the 1500s is reproduced below for those interested. Sections 1.10.32 and 1.10.33 from "de Finibus Bonorum et Malorum" by Cicero are also reproduced in their exact original</p><div class="who">Wiral Customer Name</div></div>
<div class="testi" style="left:785px"><div class="quote">&ldquo;</div><div class="avatar" role="img" aria-label="Customer portrait"></div><p>The standard chunk of Lorem Ipsum used since the 1500s is reproduced below for those interested. Sections 1.10.32 and 1.10.33 from "de Finibus Bonorum et Malorum" by Cicero are also reproduced in their exact original</p><div class="who">Wiral Customer Name</div></div>

<div class="abs cta">
  <h3>Please Contact Us To Schedule A Time For Your Visit.</h3>
  <div class="btn">Contact Us</div>
</div>

<div class="heading" style="top:2094px">Our Work</div>
<div class="rule" style="top:2145px"></div>
<div class="work" style="left:111px"><div class="pic" role="img" aria-label="Photo of health care staff in a training session"></div><h4>Training for Health care</h4><span>News &amp; Events</span></div>
<div class="work" style="left:445px"><div class="pic" role="img" aria-label="Photo of a group health care training class" style="background:linear-gradient(120deg,#5a6c80,#c9d3dc 55%,#eef0f2)"></div><h4>Training for Health care</h4><span>News &amp; Events</span></div>
<div class="work" style="left:780px"><div class="pic" role="img" aria-label="Photo of a first aid training session" style="background:linear-gradient(120deg,#e7e9ec,#c8d6e6 50%,#d9a36a)"></div><h4>Training for Health care</h4><span>News &amp; Events</span></div>

<div class="abs footer">
  <div class="btn">Request a Housecall</div>
  <div class="social" style="left:518px;top:50px"><span></span><span></span><span></span><span></span><span></span></div>
  <div class="rights">All Rights Reserved</div>
  <div class="brand" style="left:960px;top:14px"><div class="dot"></div><div class="name">VELLISANT</div></div>
</div>

</body>
</html>
```